Website for Dental Office - The Bright Arch Clinic

The bright arch clinic is a dental office offering cosmetic dentistry, general dentistry, and multi-specialty dental care all under one roof in our state-of-the-art cosmetic dental center. We are particularly striving to provide services that fit the need of the young generation. Thus, we hope to have a modern, professional concise website that represents our spirit.

*Should be able to switch from English to Chinese

6 sections besides homepage:
Home, Meet us, Services,
Patient Info, Cases&Reviews, Blog, Contact

The Services sections should contain multiple subsections such as cleaning and prevention, cosmetic dentistry, implant dentistry, removable dentures, etc...
The Patient Info section is also intended to contain several subsections such as
New Patient offer, accepted Insurance, patient portal, helpful tips, etc...

Target Market(s)

young generation

Coding

Coded - Design and coding required

Number of Pages Required

5+ page

Font styles to use
Sans Serif

Colors
0592cd
33a6d7
85cae6
00a990
33b8a4
86cfc6
cee9f5
cfeae6
3277b5

Requirements
Must have
• *Should be able to switch from English to Chinese
Nice to have
• http://www.thebrightarchclinic.com/
• As a reference, the above link is the current website, but we would like to change the appearance and the content (our new logo's picture is attached)

```html
<!DOCTYPE html>
<html lang="en">
<head>
<meta charset="utf-8">
<title>Reviews – The Bright Arch Clinic</title>
<link href="https://fonts.googleapis.com/css2?family=Montserrat:wght@400;500;600;700;800&display=swap" rel="stylesheet">
<style>
:root{
  --blue:#0592cd;
  --blue-mid:#33a6d7;
  --blue-light:#85cae6;
  --blue-pale:#dbf1fb;
  --navy:#3277b5;
  --teal:#00a990;
  --teal-mid:#33b8a4;
  --star:#f7941d;
  --ink:#111;
  --text:#555;
  --grey-bg:#f0f0f0;
  --grey-bar:#e8e8e8;
}
*{margin:0;padding:0;box-sizing:border-box}
html,body{width:893px;height:1200px;overflow:hidden}
body{position:relative;font-family:"Montserrat",sans-serif;color:var(--text);
  background:linear-gradient(#fff 0,#fff 927px,var(--grey-bg) 927px)}
.hero-bg{position:absolute;left:0;top:0;width:893px;height:440px;
  background:linear-gradient(var(--blue-pale) 20%,#fff 100%)}
.top-line{position:absolute;left:0;top:0;width:893px;height:2px;background:var(--navy)}
.header-curve{position:absolute;left:0;top:0}
.brand{position:absolute;left:120px;top:13px;display:flex;align-items:center;gap:7px}
.brand-mark{width:30px;height:30px;background:var(--blue-mid);border-radius:3px}
.brand-name{font-weight:700;color:var(--blue-mid);font-size:12px;line-height:13px;letter-spacing:.3px}
.nav{position:absolute;left:0;top:29px;width:893px;height:12px;font-size:7.2px;font-weight:500;color:#444;white-space:nowrap}
.nav span{position:absolute;top:0}
.nav .active{color:var(--teal)}
.phone-badge{position:absolute;left:643px;top:-12px;width:84px;height:84px;border-radius:50%;background:var(--navy);
  color:#fff;text-align:center;font-weight:700;font-size:9.5px;padding-top:24px}
.phone-badge svg{display:block;margin:0 auto 8px}
.lang{position:absolute;left:735px;top:22px;width:38px;height:22px;background:var(--teal);border-radius:2px;
  color:#fff;font-size:7px;display:flex;align-items:center;justify-content:center;gap:3px}
.page-title{position:absolute;top:160px;width:893px;text-align:center;font-size:31px;font-weight:800;color:var(--ink);letter-spacing:.5px}
.page-intro{position:absolute;top:208px;left:246px;width:400px;text-align:center;font-size:8px;line-height:14.5px;color:#444}
.review{position:absolute;width:313px;background:#fff;box-shadow:0 0 8px rgba(133,202,230,.35);padding:30px 18px 0}
.review .quote{display:block;margin-bottom:12px}
.review p{font-size:8.1px;line-height:14.5px;color:#444}
.reviewer{display:flex;align-items:center;gap:6px;margin-top:14px;font-size:8.3px;font-weight:700;color:var(--blue)}
.stars{display:flex;gap:2px}
.cta{position:absolute;left:120px;top:855px;width:653px;height:123px}
.cta-body{position:absolute;left:16px;top:58px;color:#fff}
.cta-body small{font-size:8.3px;display:block}
.cta-body h2{font-size:26.5px;font-weight:700;letter-spacing:.4px;margin-top:3px}
.cta-btn{position:absolute;left:463px;top:70px;width:167px;height:33px;border-radius:17px;background:#fff;
  color:var(--ink);font-size:9px;font-weight:700;display:flex;align-items:center;justify-content:center;letter-spacing:.3px}
.foot-brand{position:absolute;left:107px;top:1022px;width:170px;text-align:center}
.foot-mark{width:58px;height:52px;background:var(--blue-light);border-radius:4px;margin:0 auto 8px}
.foot-name{font-weight:700;color:var(--blue-mid);font-size:9.8px;white-space:nowrap}
.social{display:flex;gap:6px;justify-content:center;margin-top:9px}
.social span{width:25px;height:25px;border-radius:50%}
.col{position:absolute;top:1020px;font-size:7.8px;color:#555}
.col h3{font-size:8.5px;font-weight:700;color:#222;letter-spacing:.3px;margin-bottom:10px}
.col li{list-style:none;line-height:14px}
.hours td{line-height:14px;padding:0}
.hours td+td{padding-left:6px;font-weight:700;color:#333}
.contact-row{display:flex;gap:10px;margin-bottom:8px;line-height:14px;align-items:flex-start}
.contact-row .big{font-size:10.5px;color:#444;font-weight:500}
.bottom-bar{position:absolute;left:0;top:1166px;width:893px;height:34px;background:var(--grey-bar);
  display:flex;justify-content:space-between;align-items:center;padding:0 120px 0 121px;font-size:7.8px;color:#888}
.bottom-bar a{color:var(--navy);text-decoration:none}
.bottom-bar .right{color:var(--teal)}
</style>
</head>
<body>
<svg width="0" height="0" style="position:absolute">
  <symbol id="star" viewBox="0 0 24 24"><path fill="#f7941d" d="M12 1.5l3.2 7 7.6.8-5.7 5.1 1.6 7.5L12 18l-6.7 3.9 1.6-7.5L1.2 9.3l7.6-.8z"/></symbol>
  <symbol id="quote" viewBox="0 0 28 22"><g fill="none" stroke="#00a990" stroke-width="1.3"><path d="M11 2C5 3 1 8 1 14a5 5 0 1 0 5-5"/><path d="M26 2c-6 1-10 6-10 12a5 5 0 1 0 5-5"/></g></symbol>
</svg>

<div class="hero-bg"></div>
<svg class="header-curve" width="893" height="115" viewBox="0 0 893 115"><path d="M0 0H893V50Q446 160 0 50Z" fill="#fff"/></svg>
<div class="top-line"></div>

<header>
  <div class="brand"><span class="brand-mark"></span><span class="brand-name">THE BRIGHT<br>ARCH CLINIC</span></div>
  <nav class="nav">
    <span style="left:296px">HOME</span><span style="left:334px">MEET US</span><span style="left:383px">SERVICES</span><span style="left:436px">PATIENT INFO</span><span class="active" style="left:506px">REVIEWS</span><span style="left:556px">BLOG</span><span style="left:594px">CONTACT</span>
  </nav>
  <div class="phone-badge">
    <svg width="16" height="16" viewBox="0 0 24 24"><path fill="#fff" d="M6.6 10.8a15 15 0 0 0 6.6 6.6l2.2-2.2c.3-.3.7-.4 1-.2 1.1.4 2.3.6 3.6.6.6 0 1 .4 1 1V20c0 .6-.4 1-1 1A17 17 0 0 1 3 4c0-.6.4-1 1-1h3.5c.6 0 1 .4 1 1 0 1.3.2 2.5.6 3.6.1.3 0 .7-.2 1z"/></svg>
    555.014.2298
  </div>
  <div class="lang">汉语
    <svg width="7" height="5" viewBox="0 0 10 6"><path d="M1 1l4 4 4-4" stroke="#fff" stroke-width="1.6" fill="none"/></svg>
  </div>
</header>

<h1 class="page-title">REVIEWS</h1>
<p class="page-intro">Lorem Ipsum is dummy text of the printing and typesetting industry. Lorem Ipsum has been the industry's standard dummy text.</p>

<article class="review" style="left:120px;top:268px;height:145px">
  <svg class="quote" width="26" height="20"><use href="#quote"/></svg>
  <p>Friendly staff, pleasant atmosphere, great on time, and a very engaged doctor. Highly recommended!</p>
  <div class="reviewer">– Priya Nandal <span class="stars"><svg width="12" height="12"><use href="#star"/></svg><svg width="12" height="12"><use href="#star"/></svg><svg width="12" height="12"><use href="#star"/></svg><svg width="12" height="12"><use href="#star"/></svg><svg width="12" height="12"><use href="#star"/></svg></span></div>
</article>
<article class="review" style="left:460px;top:268px;height:145px">
  <svg class="quote" width="26" height="20"><use href="#quote"/></svg>
  <p>Both of my boys have been treated here. Great service. I recommend them to a friend.</p>
  <div class="reviewer">– Marcus Delgren <span class="stars"><svg width="12" height="12"><use href="#star"/></svg><svg width="12" height="12"><use href="#star"/></svg><svg width="12" height="12"><use href="#star"/></svg><svg width="12" height="12"><use href="#star"/></svg><svg width="12" height="12"><use href="#star"/></svg></span></div>
</article>
<article class="review" style="left:120px;top:441px;height:134px">
  <svg class="quote" width="26" height="20"><use href="#quote"/></svg>
  <p>Amazing place. I wish they had dental services for adults;) !</p>
  <div class="reviewer">– Lena Vorhaus <span class="stars"><svg width="12" height="12"><use href="#star"/></svg><svg width="12" height="12"><use href="#star"/></svg><svg width="12" height="12"><use href="#star"/></svg><svg width="12" height="12"><use href="#star"/></svg><svg width="12" height="12"><use href="#star"/></svg></span></div>
</article>
<article class="review" style="left:460px;top:441px;height:134px">
  <svg class="quote" width="26" height="20"><use href="#quote"/></svg>
  <p>Great service. Everyone was so friendly!</p>
  <div class="reviewer">– Owen Brackley <span class="stars"><svg width="12" height="12"><use href="#star"/></svg><svg width="12" height="12"><use href="#star"/></svg><svg width="12" height="12"><use href="#star"/></svg><svg width="12" height="12"><use href="#star"/></svg><svg width="12" height="12"><use href="#star"/></svg></span></div>
</article>
<article class="review" style="left:120px;top:603px;height:190px">
  <svg class="quote" width="26" height="20"><use href="#quote"/></svg>
  <p>I have been coming to see Dr. Hollis for over a year now. She has been nothing but amazing! Her staff is wonderful and makes you feel like you're family from the moment you walk in the door. I cannot say enough good things about her and her office!</p>
  <div class="reviewer">– Clara Mendel <span class="stars"><svg width="12" height="12"><use href="#star"/></svg><svg width="12" height="12"><use href="#star"/></svg><svg width="12" height="12"><use href="#star"/></svg><svg width="12" height="12"><use href="#star"/></svg><svg width="12" height="12"><use href="#star"/></svg></span></div>
</article>
<article class="review" style="left:460px;top:603px;height:190px">
  <svg class="quote" width="26" height="20"><use href="#quote"/></svg>
  <p>I LOVE everyone at this office!! Dr. Hollis is the best of the best. The office staff are always courteous and kind, even kept an eye on my granddaughter who was watching TV while I was being seen. They are professional, nice, outgoing, friendly––just what every office strives to be––they have it all!!</p>
  <div class="reviewer">– Ruth Ellery <span class="stars"><svg width="12" height="12"><use href="#star"/></svg><svg width="12" height="12"><use href="#star"/></svg><svg width="12" height="12"><use href="#star"/></svg><svg width="12" height="12"><use href="#star"/></svg><svg width="12" height="12"><use href="#star"/></svg></span></div>
</article>

<section class="cta">
  <svg width="653" height="123" viewBox="0 0 653 123" style="position:absolute;left:0;top:0">
    <defs><linearGradient id="ctaGrad" x1="0" x2="1"><stop offset="0" stop-color="#0592cd"/><stop offset="1" stop-color="#00a990"/></linearGradient></defs>
    <path d="M4 0L648 33Q653 34 653 38V119Q653 123 649 123H4Q0 123 0 119V4Q0 0 4 0Z" fill="url(#ctaGrad)"/>
  </svg>
  <div class="cta-body">
    <small>Lorem Ipsum is dummy text of the printing and typesetting.</small>
    <h2>YOUR SMILE. OUR PASSION.</h2>
  </div>
  <div class="cta-btn">BOOK AN APPOINTMENT</div>
</section>

<footer>
  <div class="foot-brand">
    <div class="foot-mark"></div>
    <div class="foot-name">THE BRIGHT ARCH CLINIC</div>
    <div class="social" aria-label="Social links">
      <span style="background:var(--blue)"></span><span style="background:var(--navy)"></span><span style="background:var(--teal)"></span><span style="background:var(--blue-mid)"></span>
    </div>
  </div>
  <div class="col" style="left:290px">
    <h3>USEFUL LINKS</h3>
    <ul><li>Home</li><li>Meet Us</li><li>Services</li><li>Patient Info</li><li>Case &amp; Reviews</li><li>Blog</li><li>Contact</li></ul>
  </div>
  <div class="col" style="left:459px">
    <h3>OPENING HOURS</h3>
    <table class="hours">
      <tr><td>Sunday &amp; Monday</td><td>Closed</td></tr>
      <tr><td>Tuesday</td><td>9:30AM – 5:00PM</td></tr>
      <tr><td>Wednesday</td><td>Closed</td></tr>
      <tr><td>Thursday</td><td>9:30AM – 5:00PM</td></tr>
      <tr><td>Friday</td><td>9:00AM – 5:00PM</td></tr>
      <tr><td>Saturday</td><td>9:00AM – 5:00PM</td></tr>
    </table>
  </div>
  <div class="col" style="left:629px">
    <h3>CONTACT INFO</h3>
    <div class="contact-row">
      <svg width="9" height="12" viewBox="0 0 12 16" style="margin-top:2px"><path fill="#00a990" d="M6 0a6 6 0 0 0-6 6c0 4.5 6 10 6 10s6-5.5 6-10a6 6 0 0 0-6-6zm0 8.5A2.5 2.5 0 1 1 6 3.5a2.5 2.5 0 0 1 0 5z"/></svg>
      <span>720 Harbor Lane, Suite 210,<br>Westfield MA 01085</span>
    </div>
    <div class="contact-row" style="align-items:center">
      <svg width="10" height="10" viewBox="0 0 24 24"><path fill="#3277b5" d="M6.6 10.8a15 15 0 0 0 6.6 6.6l2.2-2.2c.3-.3.7-.4 1-.2 1.1.4 2.3.6 3.6.6.6 0 1 .4 1 1V20c0 .6-.4 1-1 1A17 17 0 0 1 3 4c0-.6.4-1 1-1h3.5c.6 0 1 .4 1 1 0 1.3.2 2.5.6 3.6.1.3 0 .7-.2 1z"/></svg>
      <span class="big">555.014.2298</span>
    </div>
    <div class="contact-row" style="align-items:center">
      <svg width="11" height="8" viewBox="0 0 22 16"><rect width="22" height="16" rx="2" fill="#33a6d7"/><path d="M1 2l10 7 10-7" stroke="#fff" stroke-width="1.6" fill="none"/></svg>
      <span>info@thebrightarchclinic.com</span>
    </div>
  </div>
  <div class="bottom-bar">
    <span>© <a href="http://www.thebrightarchclinic.com/">The Bright Arch Clinic</a> – 2019. All Rights Reserved.</span>
    <span class="right">Westfield Cosmetic Care</span>
  </div>
</footer>
</body>
</html>
```